Website design for a high-end equestrian business

Design a website to replace current one. Clean, simple, elegant design. I run a business training show jumping riders and horses, as well as buying and selling high quality horses. I run my business from a beautiful yard in Co. Ardcastle, Ireland. Reference to Ireland and quality sport horses is important in the website.

Current website is www.orlathornbury.com. One page in particular that I need is a "Sport Horses" page as well as a "References" page. Layout for each to be similar to this one - https://www.brackenleaze.net/en/sporthorses

Another website I like the feel of is www.topcanterstable.com
Colour theme to be charcoal grey with elements of lighter grey and cream, as per logo. Charcoal grey to be somewhat transparent, otherwise it takes over too much. Cream colour is also to be subtle and not too beige.

Please note that Thornbury is one word.

Please note there are new photographs with which to work if desired.

Sick

Target Market(s)

Upmarket clients seeking high quality coaching services and high quality show jumping horses

Number of Pages Required

2 page

Font styles to use
Serif
Sans Serif

Colors

Designer to choose only greyscale colors for use in the design.

Requirements
Must have
• A clean, simple, elegant look to the final design. OVerall theme colours must be subtle and include charcoal grey, light grey and cream. A design that will work well for mobile also. Please include only photographs provided or on the old website.
Nice to have
• artistically integrated photographs. use of the logo.
Should not have
• Anything fussy.

```html
<!DOCTYPE html>
<html lang="en">
<head>
<meta charset="utf-8">
<title>Orla Thornbury – Home page concepts</title>
<link href="https://fonts.googleapis.com/css2?family=Montserrat:wght@500;600;700;800&family=Lato:wght@400;700&display=swap" rel="stylesheet">
<style>
:root{
  --board:#cbcbcb;
  --page:#606060;
  --header:#5b5b5b;
  --panel:#3e3e3e;
  --footer:#3b3b3b;
  --gold:#c4ae78;
  --gold-light:#d9c99c;
  --white:#ffffff;
  --text-soft:#e2e2e2;
  --field:#ffffff;
}
*{box-sizing:border-box;margin:0;padding:0}
html,body{width:837px;height:1200px;overflow:hidden}
body{background:var(--board);position:relative;font-family:"Lato",sans-serif;color:var(--white)}
.page{position:absolute;top:34px;width:337px;height:1131px;background:var(--page);overflow:hidden;border-top:1px solid var(--gold)}
.page--a{left:63px}
.page--b{left:437px}
.abs{position:absolute}

/* header */
.site-header{left:0;top:0;width:337px;height:31px;background:var(--header)}
.brand{left:41px;top:6px;display:flex;align-items:center;gap:4px;font-family:"Montserrat",sans-serif;font-weight:600;font-size:13px;color:var(--white)}
.brand-dot{width:9px;height:9px;border-radius:50%;border:1px solid var(--gold)}
.social{left:169px;top:4px;display:flex;gap:3px}
.social span{width:9px;height:9px;border-radius:50%;border:0.8px solid var(--gold)}
.lang{left:224px;top:3px;width:72px;height:10px;background:var(--field);color:#777;font-size:3.4px;padding:3px 4px;display:flex;justify-content:space-between}
.nav{right:41px;top:21px;display:flex;gap:6px;font-family:"Montserrat",sans-serif;font-weight:700;font-size:3.4px;letter-spacing:.1px}
.nav .active{color:var(--gold)}

/* hero */
.hero{left:0;top:31px;width:337px;height:208px;background:linear-gradient(160deg,#4a4a4a 0%,#7a7a7a 45%,#9d9d9d 70%,#6a6a6a 100%)}
.hero-title{left:0;top:86px;width:337px;text-align:center;font-family:"Montserrat",sans-serif;font-weight:800;font-size:21px;letter-spacing:.3px}
.hero-title em{font-style:normal;color:var(--gold)}
.scroll-mouse{left:315px;top:193px;width:6px;height:10px;border:0.8px solid var(--white);border-radius:3px}
.hero-wave{left:0;top:180px}

/* welcome */
.welcome-photo{left:41px;top:241px;width:109px;height:109px;border-radius:50%;background:radial-gradient(circle at 50% 45%,#8a5a36 0%,#4b5a4a 55%,#3a4f7a 100%);border:2px solid var(--gold)}
.welcome-shape{left:40px;top:243px;width:121px;height:113px;border-radius:40px 10px 50px 20px;background:linear-gradient(140deg,#8a7c5c 0%,#5f6d8c 50%,#b8a45a 100%);opacity:.8}
.mark{width:14px;height:14px;border-radius:50%;border:0.8px solid var(--gold)}
.welcome-mark{left:166px;top:243px}
.welcome-title{left:166px;top:260px;font-family:"Montserrat",sans-serif;font-weight:700;font-size:11.5px}
.welcome-text{left:166px;top:280px;width:132px;font-size:3.5px;line-height:7.4px;color:var(--text-soft)}
.btn{background:var(--gold);color:var(--white);font-family:"Montserrat",sans-serif;font-weight:700;font-size:3.8px;display:flex;align-items:center;justify-content:center;gap:2px}
.btn i{width:3.4px;height:3.4px;border-radius:50%;background:var(--white);display:inline-block}
.welcome-btn{left:166px;top:332px;width:42px;height:12px}

/* panels */
.panel{left:41px;width:255px;background:var(--panel)}
.panel .mark{position:absolute;left:120px;top:8px}
.panel-title{position:absolute;left:0;width:100%;text-align:center;font-family:"Montserrat",sans-serif;font-weight:700;font-size:11.5px;letter-spacing:.2px}
.arrow{position:absolute;width:4px;height:4px;border-left:1px solid var(--white);border-bottom:1px solid var(--white)}
.arrow.prev{left:9px;transform:rotate(45deg)}
.arrow.next{right:9px;transform:rotate(-135deg)}
.thumb{position:absolute;width:51px;height:46px;background:#4a4a4a}
.thumb-photo{width:51px;height:36px}
.thumb-label{font-family:"Lato",sans-serif;font-weight:700;font-size:3px;text-align:center;padding-top:3px;color:var(--text-soft)}
.tag{position:absolute;right:2px;top:3px;background:#333;font-size:3.4px;font-weight:700;padding:1px 2px}
.offer{position:absolute;left:0;top:0;width:51px;height:46px;background:linear-gradient(160deg,#b89a66,#8e6c43);border:1px solid var(--gold-light);text-align:center;font-family:"Lato",sans-serif}
.offer b{display:block;font-size:4.2px;margin-top:12px}
.offer strong{display:block;font-size:6.5px;margin-top:1px}
.offer small{display:block;font-size:2.8px;margin-top:1px}
.album{position:absolute;width:68px;height:62px;background:#4a4a4a}
.album .thumb-photo{width:68px;height:48px}
.album .thumb-label{font-size:4.2px;padding-top:4px}

.p-brown{background:linear-gradient(150deg,#6d7b63,#8a5530 60%,#5c4a3a)}
.p-field{background:linear-gradient(170deg,#7f9564,#6f5a40 65%,#8da06a)}
.p-arena{background:linear-gradient(170deg,#7a8aa8,#a66b3c 60%,#6f7d63)}
.p-crowd{background:linear-gradient(170deg,#a85a6a,#6b6f8a 45%,#b07a3c)}
.p-blue{background:linear-gradient(170deg,#4c6a9c,#8a6040 55%,#b0a04a)}
.p-grey{background:linear-gradient(160deg,#3a3a3a,#9a9a9a 55%,#5a5a5a)}
.p-light{background:linear-gradient(160deg,#c8d6e2,#d8b89a 55%,#3e6a8a)}
.p-green{background:linear-gradient(170deg,#7ab04a,#8a5a30 60%,#5a8c3a)}

/* footer */
.footer-wave{left:0;top:930px}
.footer{left:0;top:990px;width:337px;height:141px;background:var(--footer)}
.contact-title{left:47px;top:1002px;font-family:"Montserrat",sans-serif;font-weight:700;font-size:11px}
.field{position:absolute;background:var(--field);color:#666;font-size:3.6px;padding:3px 6px;height:11.5px}
.submit{left:47px;top:1079px;width:55px;height:12.5px;border-radius:7px;font-size:4.4px}
.foot-brand{left:220px;top:1018px;display:flex;align-items:center;gap:4px;font-family:"Montserrat",sans-serif;font-weight:600;font-size:14px}
.address-title{left:220px;top:1048px;font-family:"Montserrat",sans-serif;font-weight:700;font-size:7.4px}
.address{left:220px;top:1062px;width:75px;font-size:3.3px;line-height:5.8px;color:var(--text-soft)}
.phone{left:220px;top:1076px;font-family:"Montserrat",sans-serif;font-weight:700;font-size:5.2px;color:var(--gold)}
.email{left:220px;top:1087px;font-size:3.3px;color:var(--text-soft)}
.footer-rule{left:41px;top:1111px;width:255px;height:0.5px;background:#555}
.copyright{left:0;top:1118px;width:337px;text-align:center;font-size:3.2px;color:var(--text-soft)}
.ico{display:inline-block;width:3px;height:3px;background:var(--gold);margin-right:2px;vertical-align:middle}
.ico.pin{border-radius:50% 50% 50% 0;transform:rotate(-45deg)}
</style>
</head>
<body>

<!-- Concept A -->
<div class="page page--a">
  <header class="abs site-header">
    <div class="abs brand">OT <span class="brand-dot"></span></div>
    <div class="abs social"><span></span><span></span><span></span><span></span></div>
    <div class="abs lang"><span>Choose your Language</span><span>⌄</span></div>
    <nav class="abs nav"><span class="active">HOME</span><span>ABOUT</span><span>HORSES</span><span>SPONSORS</span><span>FACILITIES &amp; SERVICES</span><span>GALLERY</span><span>CONTACT</span></nav>
  </header>
  <section class="abs hero" role="img" aria-label="Black and white photo of the rider in a helmet beside her horse"></section>
  <h1 class="abs hero-title">ORLA <em>THORNBURY</em></h1>
  <div class="abs scroll-mouse"></div>
  <svg class="abs hero-wave" width="337" height="80" viewBox="0 0 337 80">
    <path d="M0,60 C70,22 150,8 220,22 C270,32 310,24 337,14 L337,80 L0,80 Z" fill="#606060"/>
    <path d="M0,56 C70,18 150,4 220,18 C270,28 305,22 337,10" fill="none" stroke="#c4ae78" stroke-width="5"/>
    <path d="M0,66 C60,36 120,24 170,26" fill="none" stroke="#8a8070" stroke-width="2"/>
  </svg>
  <div class="abs welcome-photo" role="img" aria-label="Round photo of the rider jumping a fence on a bay horse"></div>
  <div class="abs mark welcome-mark"></div>
  <h2 class="abs welcome-title">WELCOME!</h2>
  <p class="abs welcome-text">From Glenmorrow in Co. Ardcastle, Orla is 28 years old and has been passionate about horses since she was small. Over the years she has achieved many successes with a variety of equine partners, from Pony National Champion two years running on Harbour Light to Senior National Champion and Leinster Cup team-member on Lough Mist in more recent years. Having completed her studies in Liffey College</p>
  <div class="abs btn welcome-btn">READ MORE <i></i></div>

  <section class="abs panel" style="top:371px;height:113px">
    <div class="mark"></div>
    <h2 class="panel-title" style="top:26px">CURRENT HORSES</h2>
    <span class="arrow prev" style="top:70px"></span><span class="arrow next" style="top:70px"></span>
    <div class="thumb" style="left:17px;top:48px"><div class="thumb-photo p-brown" role="img" aria-label="Horse head close-up"></div><div class="thumb-label">BR KILMORNA</div><span class="tag">BUY</span></div>
    <div class="thumb" style="left:73px;top:48px"><div class="thumb-photo p-field" role="img" aria-label="Rider on horse in a field"></div><div class="thumb-label">BALLY STRAND</div></div>
    <div class="thumb" style="left:130px;top:48px"><div class="thumb-photo p-arena" role="img" aria-label="Horse in the arena"></div><div class="thumb-label">BR EMMETT</div></div>
    <div class="thumb" style="left:187px;top:48px"><div class="offer"><b>KESTREL/MARE</b><strong>€ 2500</strong><small>LEISURE,9 YEARS</small></div></div>
  </section>

  <section class="abs panel" style="top:494px;height:199px">
    <div class="mark"></div>
    <h2 class="panel-title" style="top:26px">RECENT ALBUMS</h2>
    <div class="album" style="left:18px;top:54px"><div class="thumb-photo p-crowd" role="img" aria-label="Show jumping in front of a crowd"></div><div class="thumb-label">SED UT PERSPICIATIS</div></div>
    <div class="album" style="left:93px;top:54px"><div class="thumb-photo p-blue" role="img" aria-label="Horse clearing a fence"></div><div class="thumb-label">SED UT PERSPICIATIS</div></div>
    <div class="album" style="left:169px;top:54px"><div class="thumb-photo p-arena" role="img" aria-label="Horse jumping under a blue sky"></div><div class="thumb-label">SED UT PERSPICIATIS</div></div>
    <div class="album" style="left:18px;top:123px"><div class="thumb-photo p-field" role="img" aria-label="Rider with her horse"></div><div class="thumb-label">SED UT PERSPICIATIS</div></div>
    <div class="album" style="left:93px;top:123px"><div class="thumb-photo p-blue" role="img" aria-label="Horse jumping a yellow fence"></div><div class="thumb-label">SED UT PERSPICIATIS</div></div>
    <div class="album" style="left:169px;top:123px"><div class="thumb-photo p-grey" role="img" aria-label="Horse in an indoor arena"></div><div class="thumb-label">SED UT PERSPICIATIS</div></div>
  </section>

  <section class="abs panel" style="top:704px;height:112px">
    <div class="mark"></div>
    <h2 class="panel-title" style="top:26px">TESTIMONIALS</h2>
    <span class="arrow prev" style="top:68px"></span><span class="arrow next" style="top:68px"></span>
    <div class="thumb" style="left:17px;top:47px"><div class="thumb-photo p-grey" role="img" aria-label="Rider portrait"></div><div class="thumb-label">SED UT PERSPICIATIS</div></div>
    <div class="thumb" style="left:73px;top:47px"><div class="thumb-photo p-light" role="img" aria-label="Rider portrait"></div><div class="thumb-label">SED UT PERSPICIATIS</div></div>
    <div class="thumb" style="left:130px;top:47px"><div class="thumb-photo p-grey" role="img" aria-label="Rider portrait"></div><div class="thumb-label">SED UT PERSPICIATIS</div></div>
    <div class="thumb" style="left:187px;top:47px"><div class="thumb-photo p-blue" role="img" aria-label="Rider portrait"></div><div class="thumb-label">SED UT PERSPICIATIS</div></div>
  </section>

  <section class="abs panel" style="top:828px;height:112px">
    <div class="mark"></div>
    <h2 class="panel-title" style="top:26px">SPORTS HORSES</h2>
    <span class="arrow prev" style="top:68px"></span><span class="arrow next" style="top:68px"></span>
    <div class="thumb" style="left:17px;top:47px"><div class="thumb-photo p-field" role="img" aria-label="Sport horse with rider"></div><div class="thumb-label">ISADOR</div></div>
    <div class="thumb" style="left:73px;top:47px"><div class="thumb-photo p-blue" role="img" aria-label="Sport horse with rider"></div><div class="thumb-label">EDRAN</div></div>
    <div class="thumb" style="left:130px;top:47px"><div class="thumb-photo p-arena" role="img" aria-label="Sport horse jumping"></div><div class="thumb-label">BR EMMETT</div></div>
    <div class="thumb" style="left:187px;top:47px"><div class="thumb-photo p-green" role="img" aria-label="Sport horse jumping on grass"></div><div class="thumb-label">QUINTESSA</div></div>
  </section>

  <svg class="abs footer-wave" width="337" height="62" viewBox="0 0 337 62">
    <path d="M0,62 C20,40 50,28 110,30 C200,34 280,24 337,4 L337,62 Z" fill="#3b3b3b"/>
    <path d="M30,36 C90,26 150,38 210,36 C270,34 310,22 337,2" fill="none" stroke="#c4ae78" stroke-width="5"/>
    <path d="M60,30 C120,24 180,30 230,28 C280,26 315,16 337,10" fill="none" stroke="#8a8070" stroke-width="1.5"/>
  </svg>
  <footer class="abs footer"></footer>
  <h2 class="abs contact-title">CONTACT US</h2>
  <div class="field" style="left:47px;top:1023px;width:73px">First Name</div>
  <div class="field" style="left:123px;top:1023px;width:73px">Last Name</div>
  <div class="field" style="left:47px;top:1039px;width:73px">Email</div>
  <div class="field" style="left:123px;top:1039px;width:73px">Phone</div>
  <div class="field" style="left:47px;top:1055px;width:149px;height:18px">Message</div>
  <div class="abs btn submit">SUBMIT <i></i></div>
  <div class="abs foot-brand">OT <span class="brand-dot"></span></div>
  <h3 class="abs address-title">ADDRESS</h3>
  <p class="abs address"><span class="ico pin"></span>13,Lorem Ipsum is simply dummy thepr inting typesetting industry</p>
  <p class="abs phone"><span class="ico"></span>1 800 555 0142</p>
  <p class="abs email"><span class="ico"></span>info@orlathornbury.com</p>
  <div class="abs footer-rule"></div>
  <p class="abs copyright">© 2019 Orla Thornbury. All right reserved &nbsp;Term of Use &nbsp;| &nbsp;Privacy policy</p>
</div>

<!-- Concept B -->
<div class="page page--b">
  <header class="abs site-header">
    <div class="abs brand">OT <span class="brand-dot"></span></div>
    <div class="abs social"><span></span><span></span><span></span><span></span></div>
    <div class="abs lang"><span>Choose your Language</span><span>⌄</span></div>
    <nav class="abs nav"><span class="active">HOME</span><span>ABOUT</span><span>HORSES</span><span>SPONSORS</span><span>FACILITIES &amp; SERVICES</span><span>GALLERY</span><span>CONTACT</span></nav>
  </header>
  <section class="abs hero" role="img" aria-label="Black and white photo of the rider in a helmet beside her horse"></section>
  <h1 class="abs hero-title">ORLA <em>THORNBURY</em></h1>
  <div class="abs scroll-mouse"></div>
  <svg class="abs hero-wave" width="337" height="80" viewBox="0 0 337 80">
    <path d="M0,60 C70,22 150,8 220,22 C270,32 310,24 337,14 L337,80 L0,80 Z" fill="#606060"/>
    <path d="M0,56 C70,18 150,4 220,18 C270,28 305,22 337,10" fill="none" stroke="#c4ae78" stroke-width="5"/>
    <path d="M0,66 C60,36 120,24 170,26" fill="none" stroke="#8a8070" stroke-width="2"/>
  </svg>
  <div class="abs welcome-shape" role="img" aria-label="Show jumping photo set inside a large decorative shape"></div>
  <div class="abs mark welcome-mark"></div>
  <h2 class="abs welcome-title">WELCOME!</h2>
  <p class="abs welcome-text">From Glenmorrow in Co. Ardcastle, Orla is 28 years old and has been passionate about horses since she was small. Over the years she has achieved many successes with a variety of equine partners, from Pony National Champion two years running on Harbour Light to Senior National Champion and Leinster Cup team-member on Lough Mist in more recent years. Having completed her studies in Liffey College</p>
  <div class="abs btn welcome-btn">READ MORE <i></i></div>

  <section class="abs panel" style="top:371px;height:113px">
    <div class="mark"></div>
    <h2 class="panel-title" style="top:26px">CURRENT HORSES</h2>
    <span class="arrow prev" style="top:70px"></span><span class="arrow next" style="top:70px"></span>
    <div class="thumb" style="left:17px;top:48px"><div class="thumb-photo p-brown" role="img" aria-label="Horse head close-up"></div><div class="thumb-label">BR KILMORNA</div><span class="tag">BUY</span></div>
    <div class="thumb" style="left:73px;top:48px"><div class="thumb-photo p-field" role="img" aria-label="Rider on horse in a field"></div><div class="thumb-label">BALLY STRAND</div></div>
    <div class="thumb" style="left:130px;top:48px"><div class="thumb-photo p-arena" role="img" aria-label="Horse in the arena"></div><div class="thumb-label">BR EMMETT</div></div>
    <div class="thumb" style="left:187px;top:48px"><div class="offer"><b>KESTREL/MARE</b><strong>€ 2500</strong><small>LEISURE,9 YEARS</small></div></div>
  </section>

  <section class="abs panel" style="top:494px;height:199px">
    <div class="mark"></div>
    <h2 class="panel-title" style="top:26px">RECENT ALBUMS</h2>
    <div class="album" style="left:18px;top:54px"><div class="thumb-photo p-crowd" role="img" aria-label="Show jumping in front of a crowd"></div><div class="thumb-label">SED UT PERSPICIATIS</div></div>
    <div class="album" style="left:93px;top:54px"><div class="thumb-photo p-blue" role="img" aria-label="Horse clearing a fence"></div><div class="thumb-label">SED UT PERSPICIATIS</div></div>
    <div class="album" style="left:169px;top:54px"><div class="thumb-photo p-arena" role="img" aria-label="Horse jumping under a blue sky"></div><div class="thumb-label">SED UT PERSPICIATIS</div></div>
    <div class="album" style="left:18px;top:123px"><div class="thumb-photo p-field" role="img" aria-label="Rider with her horse"></div><div class="thumb-label">SED UT PERSPICIATIS</div></div>
    <div class="album" style="left:93px;top:123px"><div class="thumb-photo p-blue" role="img" aria-label="Horse jumping a yellow fence"></div><div class="thumb-label">SED UT PERSPICIATIS</div></div>
    <div class="album" style="left:169px;top:123px"><div class="thumb-photo p-grey" role="img" aria-label="Horse in an indoor arena"></div><div class="thumb-label">SED UT PERSPICIATIS</div></div>
  </section>

  <section class="abs panel" style="top:704px;height:112px">
    <div class="mark"></div>
    <h2 class="panel-title" style="top:26px">TESTIMONIALS</h2>
    <span class="arrow prev" style="top:68px"></span><span class="arrow next" style="top:68px"></span>
    <div class="thumb" style="left:17px;top:47px"><div class="thumb-photo p-grey" role="img" aria-label="Rider portrait"></div><div class="thumb-label">SED UT PERSPICIATIS</div></div>
    <div class="thumb" style="left:73px;top:47px"><div class="thumb-photo p-light" role="img" aria-label="Rider portrait"></div><div class="thumb-label">SED UT PERSPICIATIS</div></div>
    <div class="thumb" style="left:130px;top:47px"><div class="thumb-photo p-grey" role="img" aria-label="Rider portrait"></div><div class="thumb-label">SED UT PERSPICIATIS</div></div>
    <div class="thumb" style="left:187px;top:47px"><div class="thumb-photo p-blue" role="img" aria-label="Rider portrait"></div><div class="thumb-label">SED UT PERSPICIATIS</div></div>
  </section>

  <section class="abs panel" style="top:828px;height:112px">
    <div class="mark"></div>
    <h2 class="panel-title" style="top:26px">SPORTS HORSES</h2>
    <span class="arrow prev" style="top:68px"></span><span class="arrow next" style="top:68px"></span>
    <div class="thumb" style="left:17px;top:47px"><div class="thumb-photo p-field" role="img" aria-label="Sport horse with rider"></div><div class="thumb-label">ISADOR</div></div>
    <div class="thumb" style="left:73px;top:47px"><div class="thumb-photo p-blue" role="img" aria-label="Sport horse with rider"></div><div class="thumb-label">EDRAN</div></div>
    <div class="thumb" style="left:130px;top:47px"><div class="thumb-photo p-arena" role="img" aria-label="Sport horse jumping"></div><div class="thumb-label">BR EMMETT</div></div>
    <div class="thumb" style="left:187px;top:47px"><div class="thumb-photo p-green" role="img" aria-label="Sport horse jumping on grass"></div><div class="thumb-label">QUINTESSA</div></div>
  </section>

  <svg class="abs footer-wave" width="337" height="62" viewBox="0 0 337 62">
    <path d="M0,62 C20,40 50,28 110,30 C200,34 280,24 337,4 L337,62 Z" fill="#3b3b3b"/>
    <path d="M30,36 C90,26 150,38 210,36 C270,34 310,22 337,2" fill="none" stroke="#c4ae78" stroke-width="5"/>
    <path d="M60,30 C120,24 180,30 230,28 C280,26 315,16 337,10" fill="none" stroke="#8a8070" stroke-width="1.5"/>
  </svg>
  <footer class="abs footer"></footer>
  <h2 class="abs contact-title">CONTACT US</h2>
  <div class="field" style="left:47px;top:1023px;width:73px">First Name</div>
  <div class="field" style="left:123px;top:1023px;width:73px">Last Name</div>
  <div class="field" style="left:47px;top:1039px;width:73px">Email</div>
  <div class="field" style="left:123px;top:1039px;width:73px">Phone</div>
  <div class="field" style="left:47px;top:1055px;width:149px;height:18px">Message</div>
  <div class="abs btn submit">SUBMIT <i></i></div>
  <div class="abs foot-brand">OT <span class="brand-dot"></span></div>
  <h3 class="abs address-title">ADDRESS</h3>
  <p class="abs address"><span class="ico pin"></span>13,Lorem Ipsum is simply dummy thepr inting typesetting industry</p>
  <p class="abs phone"><span class="ico"></span>1 800 555 0142</p>
  <p class="abs email"><span class="ico"></span>info@orlathornbury.com</p>
  <div class="abs footer-rule"></div>
  <p class="abs copyright">© 2019 Orla Thornbury. All right reserved &nbsp;Term of Use &nbsp;| &nbsp;Privacy policy</p>
</div>

</body>
</html>
```